Exciting opportunity to create logo and a label for our natural health brand.

About us

We are a customer centric health supplement brand who believes in natural medicine and high quality ingredients. We take a holistic approach to healthcare, with an eastern philosophy. We believe in being partners with our customers in their health care journey and are invested in their well being.

Our brand philosophy and values are attached (see Vorna philosophy.png). Our personality traits are:

- Natural
- Fresh
- Modern
- Balanced (in a holistic sense)

Task breakdown

1. Design a fresh feeling logo for us
- We want it to represent our values and high quality ingredients. We would like the quality of the product to be reflected in the branding and have a high end feel.
- Logo text must include Vorna Health Sciences
- We want the Vorna to be the focus of the logo (see uploaded image Vorna logo example.png)
The logo does not have to follow this layout, but we just want the Vorna to stand out. Feel free to use your creative license on this!

2. Create an attractive label to go on the supplement bottle
- The designs need to be eye catching, give a sense of high end ingredients and natural products and tie in with the logo to give a joined up feel.
- We are selling our products online and need them to really stand out from the competition.
- See examples of labels and packaging we like (1 -7 label design).

The initial label we would like you to design would be for our product Calm Drift. It is a product that assists in the management of Anxiety and stress. The label will appear on the bottle that holds the capsules for this supplement, see uploaded files (Example plain bottles.png). The bottles may be white as the picture shows or dark blue recyclable plastic or dark brown glass . We don't have the exact dimensions of the bottle yet, but I will follow up with these.

The label needs to include the following things:
1. The logo
2. The name of the product
3. The product is to help with the relief of Anxiety and Stress
4. Number of capsules the bottle contains
5. The back of the label should have
i) The ingredients
ii) Dosage
iii) Directions of use

Please use placeholder text where needed.

We look forward to seeing your design. Thank you.

```html
<!DOCTYPE html>
<html lang="en">
<head>
<meta charset="UTF-8">
<title>Vorna Health Science – Calm Drift Label</title>
<link href="https://fonts.googleapis.com/css2?family=Barlow:wght@500;600&display=swap" rel="stylesheet">
<style>
  :root {
    --backdrop: #3a4b2b;
    --label-sage: #b1c0a5;
    --botanical-sage: #8fa784;
    --band-green: #2b3f1b;
    --ink: #0f1d15;
    --band-text: #f4f6f1;
  }
  * { margin: 0; padding: 0; box-sizing: border-box; }
  html, body {
    width: 1200px;
    height: 750px;
    overflow: hidden;
    background: var(--backdrop);
    font-family: "Barlow", "DIN Alternate", sans-serif;
  }
  .canvas {
    position: relative;
    width: 1200px;
    height: 750px;
    display: flex;
    align-items: center;
    justify-content: center;
  }
  .label {
    position: relative;
    width: 420px;
    height: 520px;
    background: var(--label-sage);
    overflow: hidden;
  }
  .botanical {
    position: absolute;
    inset: 0;
    width: 100%;
    height: 100%;
  }
  .brand {
    position: absolute;
    top: 58px;
    left: 0;
    right: 0;
    text-align: center;
    color: var(--ink);
  }
  .brand-name {
    font-weight: 600;
    font-size: 92px;
    line-height: 1;
    letter-spacing: 1px;
  }
  .brand-tagline {
    margin-top: 14px;
    font-weight: 500;
    font-size: 13px;
    letter-spacing: 9px;
    padding-left: 9px;
  }
  .product-band {
    position: absolute;
    top: 245px;
    left: 0;
    right: 0;
    height: 92px;
    background: var(--band-green);
    color: var(--band-text);
    text-align: center;
    display: flex;
    flex-direction: column;
    justify-content: center;
  }
  .product-name {
    font-weight: 600;
    font-size: 30px;
    line-height: 1.05;
    letter-spacing: 0.5px;
  }
  .product-claim {
    font-weight: 500;
    font-size: 15.5px;
    letter-spacing: 1.6px;
    margin-top: 3px;
  }
  .capsule-count {
    position: absolute;
    top: 430px;
    left: 118px;
    width: 108px;
    text-align: center;
    color: var(--ink);
  }
  .capsule-number {
    font-weight: 600;
    font-size: 24px;
    line-height: 1;
  }
  .capsule-unit {
    font-weight: 600;
    font-size: 17px;
    letter-spacing: 2px;
    line-height: 1.3;
  }
</style>
</head>
<body>
  <main class="canvas">
    <section class="label">
      <svg class="botanical" viewBox="0 0 420 520" xmlns="http://www.w3.org/2000/svg">
        <defs>
          <linearGradient id="foliageTop" x1="0" y1="0" x2="1" y2="1">
            <stop offset="0" stop-color="var(--label-sage)" stop-opacity="0"/>
            <stop offset="1" stop-color="var(--botanical-sage)" stop-opacity="0.55"/>
          </linearGradient>
          <linearGradient id="foliageBottom" x1="0" y1="1" x2="1" y2="0">
            <stop offset="0" stop-color="var(--label-sage)" stop-opacity="0"/>
            <stop offset="1" stop-color="var(--botanical-sage)" stop-opacity="0.55"/>
          </linearGradient>
        </defs>
        <rect role="img" aria-label="Line-drawn herb sprigs with leaves and flower buds" x="190" y="10" width="230" height="235" fill="url(#foliageTop)"/>
        <rect role="img" aria-label="Line-drawn herb branch with leaves" x="180" y="337" width="240" height="183" fill="url(#foliageBottom)"/>
      </svg>

      <header class="brand">
        <div class="brand-name">Vorna</div>
        <div class="brand-tagline">HEALTH SCIENCE</div>
      </header>

      <div class="product-band">
        <h1 class="product-name">Calm Drift</h1>
        <p class="product-claim">Reduce stress and anxiety naturally</p>
      </div>

      <div class="capsule-count">
        <div class="capsule-number">60</div>
        <div class="capsule-unit">capsules</div>
      </div>
    </section>
  </main>
</body>
</html>
```